Business Cards Design for the electrical wholesaler: clean bold dynamic :)

We need a business card design that would follow our latest brand guidelines. As an electrical wholesaler we want to bring a fresh look and feel into the industry. The design should be clean bold and dynamic. It should come alive with the renewed energy of our green colour. Our grey colour should keep things balanced and complement the notion of maturity and responsibility. We employ Lato as a corporate font however are not bound by this font and we’re open to interpretation here.

Target Market(s)

Electrical contractors

Industry/Entity Type

Business

Contact Information for Business Card

Logo
Name & Surname: Halyna Dorosh
Job Title: Director of Marketing
Email: halya.dorosh@quillmail.example
Cell phone: XXX.XXX.XXXX
Address: 20517 - 87 Ave. Edmonton, AB, Canada. T6K 4N8
Business Phone: 780.555.0184
Website: www.brovix.example

Font styles to use
Other font styles liked:
• Lato

Requirements
Must have
• Logo & website
Nice to have
• Brand elements - some of them you may find in the attached Brand Guidelines (e.g. three lines on the background signifying "W")

```html
<!DOCTYPE html>
<html lang="en">
<head>
<meta charset="utf-8">
<title>Brovix business card</title>
<link href="https://fonts.googleapis.com/css2?family=Lato:wght@400;700;900&display=swap" rel="stylesheet">
<style>
  :root {
    --backdrop: #3b3b3c;
    --card: #1d1d1f;
    --card-edge: #2a2a2c;
    --green: #7ac231;
    --grey: #b9b9bb;
    --grey-deep: #3c3c3f;
    --white: #f1f1f1;
  }
  * { margin: 0; padding: 0; box-sizing: border-box; }
  html, body { width: 799px; height: 1200px; overflow: hidden; }
  body {
    background: var(--backdrop);
    font-family: "Lato", sans-serif;
    display: flex;
    flex-direction: column;
    align-items: center;
    justify-content: space-around;
    padding: 110px 0;
  }
  .card {
    position: relative;
    width: 580px;
    height: 340px;
    background: var(--card);
    border: 1px solid var(--card-edge);
    border-radius: 24px;
    overflow: hidden;
  }
  .brand { display: flex; align-items: center; gap: 14px; }
  .brand-mark { width: 26px; height: 26px; background: var(--green); }
  .brand-name { font-weight: 900; color: var(--grey); letter-spacing: 1px; }

  /* front */
  .card-front { display: flex; align-items: center; justify-content: center; }
  .card-front .brand-name { font-size: 74px; }
  .card-front .brand-mark { width: 40px; height: 40px; }

  /* back */
  .accent-band {
    position: absolute; left: 0; top: 0; bottom: 0;
    width: 56px;
    background: var(--green);
  }
  .accent-line {
    position: absolute; left: 64px; top: 0; bottom: 0;
    width: 5px;
    background: var(--grey);
  }
  .card-back .brand { position: absolute; left: 108px; top: 30px; }
  .card-back .brand-name { font-size: 50px; }
  .contact {
    position: absolute; left: 108px; top: 106px;
    z-index: 2;
    color: var(--white);
    font-size: 14px;
    line-height: 20px;
  }
  .contact-name {
    color: var(--green);
    font-size: 22px;
    font-weight: 700;
    line-height: 24px;
  }
  .contact-title { margin-bottom: 8px; }
  .contact-row { display: flex; align-items: center; gap: 8px; }
  .icon { width: 16px; height: 16px; flex: none; }
  .backdrop-word {
    position: absolute; right: 14px; bottom: -16px;
    z-index: 1;
    font-size: 84px;
    line-height: 1;
    font-weight: 900;
    color: var(--grey-deep);
  }
</style>
</head>
<body>
  <section class="card card-front">
    <div class="brand">
      <span class="brand-mark"></span>
      <span class="brand-name">brovix</span>
    </div>
  </section>

  <section class="card card-back">
    <div class="accent-band"></div>
    <div class="accent-line"></div>
    <div class="brand">
      <span class="brand-mark"></span>
      <span class="brand-name">brovix</span>
    </div>
    <div class="contact">
      <p class="contact-name">Halyna Dorosh</p>
      <p class="contact-title">Director of Marketing</p>
      <p>20517 - 87 Ave. Edmonton,</p>
      <p>AB, Canada. T6K 4N8</p>
      <p class="contact-row">
        <svg class="icon" viewBox="0 0 16 16"><circle cx="8" cy="8" r="8" fill="var(--green)"/><path d="M5 4.5h2l.8 2-1.2.8a5 5 0 0 0 2.1 2.1l.8-1.2 2 .8v2a1 1 0 0 1-1 1A7 7 0 0 1 4 5.5a1 1 0 0 1 1-1z" fill="var(--card)"/></svg>
        780.555.0184
      </p>
      <p class="contact-row">
        <svg class="icon" viewBox="0 0 16 16"><circle cx="8" cy="8" r="8" fill="var(--green)"/><rect x="4" y="5" width="8" height="6" fill="var(--card)"/><path d="M4 5l4 3 4-3" stroke="var(--green)" fill="none"/></svg>
        halya.dorosh@quillmail.example
      </p>
      <p class="contact-row">
        <svg class="icon" viewBox="0 0 16 16"><circle cx="8" cy="8" r="8" fill="var(--green)"/><circle cx="8" cy="8" r="4" fill="none" stroke="var(--card)" stroke-width="1.2"/><path d="M4 8h8M8 4v8" stroke="var(--card)" stroke-width="1"/></svg>
        www.brovix.example
      </p>
    </div>
    <div class="backdrop-word" aria-hidden="true">brovix</div>
  </section>
</body>
</html>
```